Residential Remodeling Contractor needs updated business card

I need a new design for my business card.
Name of the company is Ridgefell Construction. I need a card that commands presence, strength, integrity. I have been in business for 28 years. I am a Residential Remodeling Contractor that covers all aspects of a residential remodel and build.

```html
<!DOCTYPE html>
<html lang="en">
<head>
<meta charset="utf-8">
<title>Ridgefell Construction – Business Card</title>
<link href="https://fonts.googleapis.com/css2?family=Cinzel:wght@700&family=Arimo:wght@400&display=swap" rel="stylesheet">
<style>
  :root {
    --backdrop: #9a9a9a;
    --navy: #183d7c;
    --navy-deep: #1c3673;
    --navy-light: #8ea8d8;
    --white: #ffffff;
  }
  * { margin: 0; padding: 0; box-sizing: border-box; }
  html, body { width: 1200px; height: 1059px; overflow: hidden; }
  body { background: var(--backdrop); position: relative; font-family: "Arimo", Arial, sans-serif; }

  .card {
    position: absolute;
    width: 690px;
    height: 392px;
    border-radius: 16px;
    overflow: hidden;
  }
  .card--front { left: 256px; top: 89px; background: var(--white); }
  .card--back  { left: 254px; top: 569px; }

  .front-wave { position: absolute; inset: 0; width: 100%; height: 100%; }

  .wordmark {
    position: absolute;
    font-family: "Cinzel", "Times New Roman", serif;
    font-weight: 700;
    line-height: 1;
    text-align: left;
  }
  .wordmark span { display: block; }
  .wordmark--front { right: 36px; top: 80px; color: var(--navy); font-size: 35px; }
  .wordmark--front span + span { font-size: 27px; margin-top: 8px; }
  .wordmark--back { left: 478px; top: 290px; color: var(--white); font-size: 21px; }
  .wordmark--back span + span { font-size: 16px; margin-top: 4px; }

  .person { position: absolute; left: 34px; top: 200px; color: var(--white); }
  .person__name {
    font-family: "Cinzel", "Times New Roman", serif;
    font-weight: 700;
    font-size: 21px;
    letter-spacing: 0.5px;
  }
  .person__role { font-size: 15.5px; margin-top: 2px; }

  .contacts { position: absolute; left: 34px; top: 264px; list-style: none; color: var(--white); font-size: 16.5px; }
  .contacts li { display: flex; align-items: center; height: 24px; }
  .contacts svg { width: 13px; height: 13px; margin-right: 9px; flex: none; }

  .address {
    position: absolute; right: 35px; top: 316px;
    color: var(--white); font-size: 16.5px; text-align: right; line-height: 24px;
  }

  .back-pattern {
    position: absolute; inset: 0;
    background: linear-gradient(245deg, #5f7fbe 0%, #34589f 28%, var(--navy-deep) 58%, #1f3a78 100%);
  }
</style>
</head>
<body>

<section class="card card--front">
  <svg class="front-wave" viewBox="0 0 690 392" preserveAspectRatio="none" aria-hidden="true">
    <defs>
      <linearGradient id="swoosh-left" x1="0" x2="1">
        <stop offset="0" stop-color="#183d7c" stop-opacity="0"/>
        <stop offset="0.6" stop-color="#183d7c"/>
      </linearGradient>
      <linearGradient id="swoosh-right" x1="0" x2="1">
        <stop offset="0" stop-color="#183d7c"/>
        <stop offset="1" stop-color="#183d7c" stop-opacity="0"/>
      </linearGradient>
    </defs>
    <path d="M0 176 C 60 118, 170 128, 290 186 C 390 234, 450 268, 525 264 C 590 262, 640 250, 690 220 V392 H0 Z" fill="var(--navy)"/>
    <path d="M2 156 C 60 118, 150 112, 192 136 C 150 122, 70 128, 2 168 Z" fill="url(#swoosh-left)"/>
    <path d="M85 130 C 160 120, 240 140, 330 190 C 410 236, 460 272, 503 286 C 450 272, 400 246, 320 198 C 240 150, 160 128, 85 130 Z" fill="var(--white)"/>
    <path d="M432 244 C 520 282, 610 270, 690 204 L 690 212 C 610 276, 520 290, 432 244 Z" fill="url(#swoosh-right)"/>
  </svg>

  <div class="wordmark wordmark--front"><span>Ridgefell</span><span>Construction</span></div>

  <div class="person">
    <div class="person__name">DANIEL WHITCOMBE</div>
    <div class="person__role">Owner &amp; Manager</div>
  </div>

  <ul class="contacts">
    <li>
      <svg viewBox="0 0 16 16" aria-hidden="true"><path fill="#fff" d="M1 6c0-2 3-3 7-3s7 1 7 3v1h-3V5.5H4V7H1zM4 8h8l2 6H2z"/></svg>
      555 214 7730
    </li>
    <li>
      <svg viewBox="0 0 16 16" aria-hidden="true"><rect x="4" y="1" width="8" height="14" rx="1.5" fill="none" stroke="#fff" stroke-width="1.6"/><circle cx="8" cy="12.5" r="1" fill="#fff"/></svg>
      555-318-60427
    </li>
    <li>
      <svg viewBox="0 0 16 16" aria-hidden="true"><path fill="#fff" d="M1 6l7-4 7 4v8H1zM2.5 7v5.5l4-3zm11 0l-4 2.5 4 3z"/></svg>
      info@ridgefellconstruction.com
    </li>
    <li>
      <svg viewBox="0 0 16 16" aria-hidden="true"><circle cx="8" cy="8" r="7" fill="#fff"/><path fill="var(--navy)" d="M4 4c2 0 3 1 2 3s-2 1-3 2zM9 9c2-1 4 0 3 2s-3 2-4 1z"/></svg>
      www.ridgefellconstruction.com
    </li>
  </ul>

  <div class="address">P.O. Box&nbsp; Street Name<br>Country Name AB, A5B 521</div>
</section>

<section class="card card--back">
  <div class="back-pattern" role="img" aria-label="Repeating tonal pattern of the company emblem across a navy background, brightening toward the upper right"></div>
  <div class="wordmark wordmark--back"><span>Ridgefell</span><span>Construction</span></div>
</section>

</body>
</html>
```